indépendant en tant que Massothérapeute et Préparateur Mental, j'ai besoin de ...

Massothérapeute et préparateur mental indépendant, je recherche une carte de visite sobre et dynamique, sans images liées au massage ou à la préparation mentale mais intégrant mon logo. Les couleurs que j'aime bien sont : Blanc, gris, anthracite, noir et jaune

Contact Information for Business Card

carte de préférence Horizontale
neutre qui puisse toucher le deux domaines Massothérapie et préparation mentale

Requirements
Must have
• mon projet doit intégrer au recto:
LOGO
Loïc Bardèze
078 513 26 48
info@loicbardeze.ch
et éventuellement www.loicbardeze.ch

et au verso les deux adresses:

Chemin des Ormilles 7B
1400 Yverdon-les-Bains

Route de la Gravière 9
1700 Fribourg

Should not have
• mon projet ne doit pas contenir d'image en liens avec le massage ni la préparation mentale.

```html
<!DOCTYPE html>
<html lang="fr">
<head>
<meta charset="utf-8">
<title>Loïc Bardèze – Carte de visite</title>
<link href="https://fonts.googleapis.com/css2?family=Montserrat:wght@600&family=Open+Sans:wght@400;600&display=swap" rel="stylesheet">
<style>
  :root {
    --bg: #e8e8e8;
    --ink: #2b2b2b;
    --ink-soft: #3a3a3a;
    --rule: #8a8a8a;
    --paper: #f7f7f7;
    --dark-1: #5a5a5a;
    --dark-2: #1c1c1c;
    --dark-3: #0b0b0b;
    --white: #ffffff;
  }
  * { margin: 0; padding: 0; box-sizing: border-box; }
  html, body { width: 1200px; height: 960px; overflow: hidden; }
  body { background: var(--bg); position: relative; font-family: "Open Sans", sans-serif; color: var(--ink); }

  .card { position: absolute; left: 322px; width: 558px; height: 361px; }
  .card-front { top: 102px; background: var(--dark-3); overflow: hidden; }
  .card-back { top: 495px; background: var(--paper); }

  .front-texture {
    position: absolute; inset: 0;
    background: linear-gradient(160deg, var(--dark-1) 0%, var(--dark-2) 40%, var(--dark-3) 75%);
  }
  .front-brand { position: absolute; left: 83px; top: 150px; color: var(--white); }
  .brand-name { font-family: "Montserrat", sans-serif; font-weight: 600; font-size: 31px; letter-spacing: 0.5px; line-height: 1; }
  .brand-tagline { font-family: "Montserrat", sans-serif; font-weight: 600; font-size: 14.5px; margin-top: 12px; letter-spacing: 0.3px; }

  .back-brand { position: absolute; left: 61px; top: 52px; display: flex; align-items: center; gap: 18px; }
  .brand-mark { width: 40px; height: 40px; border-radius: 50%; background: var(--ink); }
  .back-brand .brand-name { font-size: 22px; color: var(--ink); }
  .back-brand .brand-tagline { font-size: 10.5px; margin-top: 5px; color: var(--ink); }

  .holder { position: absolute; left: 61px; top: 166px; width: 437px; display: flex; align-items: center; gap: 14px; }
  .holder-name { font-weight: 600; font-size: 19px; color: var(--ink-soft); white-space: nowrap; }
  .holder-rule { flex: 1; height: 2px; background: var(--rule); }

  .contact { position: absolute; left: 61px; top: 253px; list-style: none; font-size: 14px; line-height: 20px; color: var(--ink-soft); }
  .contact li { display: flex; align-items: center; gap: 8px; }
  .contact svg { width: 13px; height: 13px; fill: var(--ink); }

  .addresses { position: absolute; left: 288px; top: 214px; font-size: 14px; line-height: 20px; color: var(--ink-soft); font-style: normal; }
  .addresses p + p { margin-top: 18px; }
</style>
</head>
<body>
  <section class="card card-front">
    <div class="front-texture" role="img" aria-label="Motif répété du monogramme en noir brillant sur fond anthracite"></div>
    <div class="front-brand">
      <div class="brand-name">Loïc Bardèze</div>
      <div class="brand-tagline">Massothérapeute / Préparateur Mental</div>
    </div>
  </section>

  <section class="card card-back">
    <div class="back-brand">
      <span class="brand-mark"></span>
      <div>
        <div class="brand-name">Loïc Bardèze</div>
        <div class="brand-tagline">Massothérapeute / Préparateur Mental</div>
      </div>
    </div>

    <div class="holder">
      <span class="holder-name">Loïc Bardèze</span>
      <span class="holder-rule"></span>
    </div>

    <ul class="contact">
      <li><svg viewBox="0 0 24 24"><path d="M6.6 10.8a15 15 0 0 0 6.6 6.6l2.2-2.2a1 1 0 0 1 1-.25 11.4 11.4 0 0 0 3.6.57 1 1 0 0 1 1 1V20a1 1 0 0 1-1 1A17 17 0 0 1 3 4a1 1 0 0 1 1-1h3.5a1 1 0 0 1 1 1c0 1.25.2 2.45.57 3.6a1 1 0 0 1-.25 1z"/></svg>078 513 26 48</li>
      <li><svg viewBox="0 0 24 24"><path d="M2 5h20v14H2zm2 2v.5l8 5 8-5V7zm0 2.8V17h16V9.8l-8 5z"/></svg>info@loicbardeze.ch</li>
      <li><svg viewBox="0 0 24 24"><path d="M12 2a10 10 0 1 0 0 20 10 10 0 0 0 0-20zm0 2c.9 1.1 1.6 2.5 2 4h-4c.4-1.5 1.1-2.9 2-4zm-2.6.5A13 13 0 0 0 7.9 8H5.3a8 8 0 0 1 4.1-3.5zM4.5 10h3.1a15 15 0 0 0 0 4H4.5a8 8 0 0 1 0-4zm5.1 0h4.8a13 13 0 0 1 0 4H9.6a13 13 0 0 1 0-4zm6.8 0h3.1a8 8 0 0 1 0 4h-3.1a15 15 0 0 0 0-4zM5.3 16h2.6c.3 1.3.8 2.5 1.5 3.5A8 8 0 0 1 5.3 16zm4.7 0h4c-.4 1.5-1.1 2.9-2 4-.9-1.1-1.6-2.5-2-4zm6.1 0h2.6a8 8 0 0 1-4.1 3.5c.7-1 1.2-2.2 1.5-3.5zm0-8c-.3-1.3-.8-2.5-1.5-3.5A8 8 0 0 1 18.7 8z"/></svg>www.loicbardeze.ch</li>
    </ul>

    <address class="addresses">
      <p>Chemin des Ormilles 7B<br>1400 Yverdon-les-Bains</p>
      <p>Route de la Gravière 9<br>1700 Fribourg</p>
    </address>
  </section>
</body>
</html>
```